Oriel Photography Business Card

I need a business card designed for a photography business based in Perth, Western Australia called Oriel Photography.

We specialise in wedding, event photography and portrait photography.

The business card must borrow the style of the attached logo.

The hex codes for the colours in the logo are:
#ED1D85 - Pink
#89C23E - Green
#37282F - Black

The name on the card will be:
Name: Tobrian
Phone: 0417395268
Website: www.orielphotography.example.com.au
Facebook: orielphotography

I am open and happy to accept creative concepts.

I’d like some space at the back for writing notes and appointment details.

```html
<!DOCTYPE html>
<html lang="en">
<head>
<meta charset="utf-8">
<title>Oriel Photography – Business Card</title>
<link href="https://fonts.googleapis.com/css2?family=Arimo:wght@400;700&display=swap" rel="stylesheet">
<style>
  :root {
    --pink: #ED1D85;
    --green: #89C23E;
    --card-black: #050505;
    --brand-grey: #37282F;
    --wordmark-grey: #3a3a3a;
    --backdrop: #e9e6e1;
  }
  * { box-sizing: border-box; margin: 0; padding: 0; }
  html, body {
    width: 1200px;
    height: 1000px;
    overflow: hidden;
    background: var(--backdrop);
    font-family: "Arimo", Arial, sans-serif;
  }
  .canvas {
    position: relative;
    width: 1200px;
    height: 1000px;
  }
  .card {
    position: absolute;
    left: 250px;
    width: 700px;
    height: 400px;
    background: var(--card-black);
    border-radius: 4px;
    box-shadow: 0 10px 28px rgba(0,0,0,0.25);
    overflow: hidden;
  }
  .card--front { top: 60px; }
  .card--back { top: 540px; }

  .brand {
    position: absolute;
    left: 0;
    width: 100%;
    display: flex;
    flex-direction: column;
    align-items: center;
  }
  .brand__dot {
    width: 72px;
    height: 72px;
    border-radius: 50%;
    background: var(--pink);
  }
  .brand__name {
    margin-top: 22px;
    font-size: 17px;
    font-weight: 400;
    letter-spacing: 9px;
    text-transform: uppercase;
    color: var(--wordmark-grey);
    padding-left: 9px;
  }
  .card--front .brand { top: 130px; }
  .card--back .brand { top: 34px; }
  .card--back .brand__dot { width: 64px; height: 64px; }
  .card--back .brand__name { margin-top: 18px; font-size: 15px; letter-spacing: 8px; }

  .divider {
    position: absolute;
    left: 0;
    top: 186px;
    width: 100%;
    height: 3px;
    background: var(--green);
  }

  .contact {
    position: absolute;
    right: 40px;
    top: 206px;
    text-align: right;
    font-size: 16px;
    line-height: 22px;
    color: var(--green);
  }
  .contact__name {
    font-size: 19px;
    font-weight: 700;
    color: var(--pink);
    margin-bottom: 10px;
  }
  .contact__label { color: var(--pink); }
</style>
</head>
<body>
<main class="canvas">
  <section class="card card--front" aria-label="Card front">
    <div class="brand">
      <span class="brand__dot"></span>
      <span class="brand__name">Oriel Photography</span>
    </div>
  </section>

  <section class="card card--back" aria-label="Card back">
    <div class="brand">
      <span class="brand__dot"></span>
      <span class="brand__name">Oriel Photography</span>
    </div>
    <div class="divider"></div>
    <div class="contact">
      <p class="contact__name">Tobrian</p>
      <p><span class="contact__label">P:</span> 0417395268</p>
      <p><span class="contact__label">W:</span> www.orielphotography.example.com.au</p>
      <p><span class="contact__label">f:</span> facebook/orielphotography</p>
    </div>
  </section>
</main>
</body>
</html>
```